Willow Nest Product Marketing Sheet Front and Back

Please see the VERY VERY VERY ROUGH COMPS THAT WE DID TO LEND SOME DIRECTION TO THE PIECE- SO YOU HAVE AN IDEA OF WHAT'S IMPORTANT TO COMMUNICATE ON THE FRONT AND THE BACK.

DON'T FOLLOW OUR LAYOUT.. This is just for you to see what goes to the front and what goes to the back.. see the files that we just loaded up to the art folder!

We also have a PDF that has a check off list for items that need to be on the front and then on the back!

PROJECT SCOPE:

Project is to make a sell sheet front that is 8.5 inches wide x 11 inches tall in a 4 color design using our current Willow Nest Logo with your design talents. We also need the back of the sell sheet that has the basic instructions on how to install the Willow Nest Mattress Cover and shows the value added aspects of the product.

We need files in layered PSD format as we have various dealers that we tweak parts of our product line. We will also use these layered files as a back up for the printer in case they don't have the printer font, we can make him print ready file from your PSD file.

We have the logo, tag line, header main font selected and need you to design the look and feel of the piece.

We have all of the copy for the sell sheet- this is the only PDF file in the art file resources.

Overall this piece needs to convey a FUN, FRESH and PEACEFUL PRODUCT.. we don't want a cluttered design.

COPY IS SAVED AS: WILLOW NEST CONTENTS ( PDF FILE)
COMPS ARE SAVED AS: FRONT AND REAR COMP ( JPG FILES)
Updates

Project Deadline Extended
Reason: We have a lot of designers that have requested a few more days to submit.. so we are extending the competition. Thank you and good luck!

Target Market(s)

Corvani Consumers that are buying a mattress cover for comfort, peace of mind and to reduce night heat issues ( sweating) and to avoid dust mites, bed bugs and stains.

Industry/Entity Type

Marketing

Font styles to use
Sans Serif

Colors
f37122
f68e4e
fabb94
0393ce
33a6d7
86cae7
ffffff
add136
fbee3d

Requirements
Must have
• Our Current Logo as the center piece..
• WILLOW NEST is the brand name
• For a peaceful night sleep is the tag line
• Value Points ( see the PDF attached)
• Crisp color, Clean Fonts, Cant be cluttered.
• File Construction- Must be a PSD file 8.5 x11 and 300 DPI for printing
Nice to have
• Clean, Easy to Read and consistent from the front to the back
Should not have
• We don't want a cluttered look and feel for this marketing piece.

```html
<!DOCTYPE html>
<html lang="en">
<head>
<meta charset="utf-8">
<title>Willow Nest Sell Sheet – Back and Front</title>
<link rel="stylesheet" href="https://fonts.googleapis.com/css2?family=Comfortaa:wght@600;700&family=Open+Sans:wght@600;700&display=swap">
<style>
  :root{
    --stage:#e6e6e6;
    --paper:#ffffff;
    --orange:#f37122;
    --orange-mid:#f68e4e;
    --orange-light:#fabb94;
    --blue:#0393ce;
    --blue-mid:#33a6d7;
    --blue-light:#86cae7;
    --green:#add136;
    --yellow:#fbee3d;
    --ink:#4a4a4a;
    --grey-soft:#ececef;
    --grey:#dedee2;
  }
  *{box-sizing:border-box;margin:0;padding:0}
  html,body{width:1200px;height:799px;overflow:hidden;background:var(--stage)}
  .canvas{position:relative;width:1200px;height:799px}
  .sheet{position:absolute;top:40px;width:556px;height:720px;background:var(--paper);overflow:hidden;box-shadow:0 6px 18px rgba(0,0,0,.15)}
  .sheet--back{left:30px}
  .sheet--front{left:614px}
  .sheet svg{position:absolute;left:0;top:0}

  /* shared badge styling */
  .badge__label{font-family:"Open Sans",sans-serif;font-weight:700;font-size:9px;fill:var(--blue)}
  .badge__disc{fill:var(--orange)}
  .badge__ring{fill:none;stroke:#fff;stroke-width:1.5}
  .badge__glyph{fill:#fff}
  .badge__line{stroke:#fff;fill:none}
  .badge__cut{fill:var(--orange)}
  .badge__cut-line{stroke:var(--orange)}

  .dots{position:absolute;left:0;right:0;bottom:0;height:200px;
    background:linear-gradient(180deg,#fff 0%,var(--grey-soft) 45%,var(--grey) 100%)}

  /* front */
  .hero-photo{position:absolute;left:190px;top:78px;width:366px;height:200px;
    background:radial-gradient(ellipse at 55% 45%,#f3dfd4 0%,#f5ece6 40%,rgba(255,255,255,0) 75%)}
  .brand{position:absolute;left:22px;top:20px;display:flex;align-items:center;gap:8px}
  .brand__dot{width:34px;height:34px;border-radius:50%;background:var(--yellow)}
  .brand__name{font-family:"Open Sans",sans-serif;font-weight:700;font-size:15px;color:var(--orange);letter-spacing:.5px}
  .tagline{position:absolute;right:22px;top:30px;text-align:right}
  .tagline__main{font-family:"Comfortaa",sans-serif;font-weight:700;font-size:25px;color:var(--blue)}
  .tagline__main em{font-style:normal;color:var(--orange)}
  .tagline__sub{font-family:"Comfortaa",sans-serif;font-weight:600;font-size:10.5px;color:var(--ink);margin-top:4px}
  .benefits{position:absolute;left:36px;top:186px;list-style:none}
  .benefits li{font-family:"Open Sans",sans-serif;font-weight:700;font-size:13.5px;color:var(--blue);line-height:1.55;text-transform:uppercase}
  .benefits li::before{content:"✓ ";color:var(--green)}
  .fits{position:absolute;left:0;right:0;bottom:48px;text-align:center;font-family:"Comfortaa",sans-serif;font-weight:700;font-size:26px;color:var(--blue);text-transform:uppercase}

  /* back */
  .steps-band{position:absolute;left:0;top:0;width:556px;height:222px;background:linear-gradient(120deg,var(--blue) 0%,var(--blue-light) 100%)}
  .steps-title{position:absolute;left:0;right:0;top:22px;text-align:center;font-family:"Comfortaa",sans-serif;font-weight:700;font-size:21px;color:#fff;text-transform:uppercase}
  .step__text{font-family:"Open Sans",sans-serif;font-weight:700;font-size:9px;fill:var(--blue)}
  .fabric-photo{position:absolute;left:34px;width:148px;height:148px;border-radius:50%;background:radial-gradient(circle at 40% 35%,#fafafa,#d8d8dc)}
  .fabric-photo--terry{top:196px;border:6px solid var(--orange)}
  .fabric-photo--quilt{top:356px;border:6px solid var(--blue)}
  .sizes{position:absolute;left:0;right:0;top:518px;text-align:center}
  .sizes__title{font-family:"Comfortaa",sans-serif;font-weight:700;font-size:18px;color:var(--blue);text-transform:uppercase}
  .sizes__list{font-family:"Open Sans",sans-serif;font-weight:700;font-size:13px;color:var(--ink);margin-top:6px}
  .pillow-photo{position:absolute;left:40px;top:600px;width:190px;height:84px;border-radius:30px;background:radial-gradient(ellipse at 50% 45%,#ffffff 0%,#ececee 60%,#d6d6da 100%)}
  .offer{position:absolute;left:296px;top:610px}
  .offer__title{font-family:"Comfortaa",sans-serif;font-weight:700;font-size:17px;color:var(--orange);text-transform:uppercase}
  .offer__text{font-family:"Comfortaa",sans-serif;font-weight:700;font-size:16px;color:#666;margin-top:6px;line-height:1.35}
</style>
</head>
<body>
<main class="canvas">

  <section class="sheet sheet--back" aria-label="Sell sheet back">
    <div class="dots" role="img" aria-label="Soft grey dotted band"></div>
    <div class="steps-band"></div>
    <h2 class="steps-title">3 Simple Steps</h2>

    <svg width="556" height="222" viewBox="0 0 556 222" aria-label="Installation steps">
      <g class="step__text" text-anchor="middle">
        <circle cx="110" cy="128" r="50" fill="#fff"/>
        <text x="110" y="124">STEP 1</text><text x="110" y="137">ALIGN CORNERS</text>
        <circle cx="278" cy="128" r="50" fill="#fff"/>
        <text x="278" y="124">STEP 2</text><text x="278" y="137">STRETCH OVER</text>
        <circle cx="446" cy="128" r="50" fill="#fff"/>
        <text x="446" y="124">STEP 3</text><text x="446" y="137">SMOOTH FLAT</text>
      </g>
      <g stroke="#fff" stroke-width="2.5" fill="none" stroke-linecap="round">
        <path d="M176 128h36M204 120l8 8-8 8"/>
        <path d="M344 128h36M372 120l8 8-8 8"/>
      </g>
    </svg>

    <div class="fabric-photo fabric-photo--terry" role="img" aria-label="Close-up of the terry cloth surface"></div>
    <div class="fabric-photo fabric-photo--quilt" role="img" aria-label="Mattress with the fitted cover installed"></div>

    <svg width="556" height="520" viewBox="0 0 556 520" aria-label="Product features">
      <defs><path id="arcB" d="M-42 0 A42 42 0 0 1 42 0"/></defs>
      <g class="badge__label">
        <g transform="translate(290 300)">
          <text><textPath href="#arcB" startOffset="50%" text-anchor="middle">NO NOISE</textPath></text>
          <circle class="badge__disc" r="32"/><circle class="badge__ring" r="26"/>
          <circle class="badge__line" r="11" stroke-width="2.5"/><path class="badge__line" d="M-9 9L9-9" stroke-width="2.5"/>
        </g>
        <g transform="translate(430 300)">
          <text><textPath href="#arcB" startOffset="50%" text-anchor="middle">WATERPROOF</textPath></text>
          <circle class="badge__disc" r="32"/><circle class="badge__ring" r="26"/>
          <path class="badge__glyph" d="M0-13Q10 0 10 5A10 10 0 0 1-10 5Q-10 0 0-13Z"/>
        </g>
        <g transform="translate(290 430)">
          <text><textPath href="#arcB" startOffset="50%" text-anchor="middle">WASHABLE</textPath></text>
          <circle class="badge__disc" r="32"/><circle class="badge__ring" r="26"/>
          <rect class="badge__glyph" x="-11" y="-13" width="22" height="26" rx="3"/><circle class="badge__cut" cy="3" r="6"/>
        </g>
        <g transform="translate(430 430)">
          <text><textPath href="#arcB" startOffset="50%" text-anchor="middle">SOFT TERRY</textPath></text>
          <circle class="badge__disc" r="32"/><circle class="badge__ring" r="26"/>
          <path class="badge__glyph" d="M-11 11Q-4-12 12-12Q9 5-11 11Z"/>
        </g>
      </g>
    </svg>

    <div class="sizes">
      <p class="sizes__title">Available in these sizes:</p>
      <p class="sizes__list">CAL KING, KING, QUEEN, DOUBLE, TWIN</p>
    </div>

    <div class="pillow-photo" role="img" aria-label="White bed pillow"></div>
    <div class="offer">
      <p class="offer__title">We also offer:</p>
      <p class="offer__text">Willow Nest Pillows<br>and Pillow Cases</p>
    </div>
  </section>

  <section class="sheet sheet--front" aria-label="Sell sheet front">
    <div class="dots" role="img" aria-label="Soft grey dotted band"></div>
    <div class="hero-photo" role="img" aria-label="Woman sleeping peacefully on a white pillow"></div>

    <div class="brand">
      <span class="brand__dot"></span>
      <span class="brand__name">WILLOW NEST</span>
    </div>

    <div class="tagline">
      <p class="tagline__main">for a <em>peaceful</em> night sleep</p>
      <p class="tagline__sub">Terry Cloth Waterproof Mattress Protection</p>
    </div>

    <ul class="benefits">
      <li>Five sided protection</li>
      <li>Elastic corners for extra grip</li>
      <li>No slip mattress protection</li>
    </ul>

    <svg width="556" height="720" viewBox="0 0 556 720" aria-label="Product features">
      <defs><path id="arcF" d="M-50 0 A50 50 0 0 1 50 0"/></defs>
      <g class="badge__label">
        <g transform="translate(85 345)">
          <text><textPath href="#arcF" startOffset="50%" text-anchor="middle">QUITE- NO NOISE</textPath></text>
          <circle class="badge__disc" r="40"/><circle class="badge__ring" r="33"/>
          <circle class="badge__line" r="14" stroke-width="3"/><path class="badge__line" d="M-11 11L11-11" stroke-width="3"/>
        </g>
        <g transform="translate(210 345)">
          <text><textPath href="#arcF" startOffset="50%" text-anchor="middle">ULTRA SOFT TERRY CLOTH</textPath></text>
          <circle class="badge__disc" r="40"/><circle class="badge__ring" r="33"/>
          <path class="badge__glyph" d="M-14 14Q-5-15 16-15Q12 6-14 14Z"/><path class="badge__cut-line" d="M-16 16L10-9" stroke-width="1.5"/>
        </g>
        <g transform="translate(335 345)">
          <text><textPath href="#arcF" startOffset="50%" text-anchor="middle">WATERPROOF</textPath></text>
          <circle class="badge__disc" r="40"/><circle class="badge__ring" r="33"/>
          <path class="badge__glyph" d="M0-17Q13 0 13 6A13 13 0 0 1-13 6Q-13 0 0-17Z"/>
        </g>
        <g transform="translate(460 345)">
          <text><textPath href="#arcF" startOffset="50%" text-anchor="middle">SWEAT STAIN BLOCKER</textPath></text>
          <circle class="badge__disc" r="40"/><circle class="badge__ring" r="33"/>
          <circle class="badge__glyph" r="12"/><circle class="badge__glyph" cx="15" cy="-9" r="3.5"/><circle class="badge__glyph" cx="-14" cy="11" r="3"/><circle class="badge__glyph" cx="-10" cy="-15" r="2.5"/>
        </g>
        <g transform="translate(85 480)">
          <text><textPath href="#arcF" startOffset="50%" text-anchor="middle">WASHABLE</textPath></text>
          <circle class="badge__disc" r="40"/><circle class="badge__ring" r="33"/>
          <rect class="badge__glyph" x="-13" y="-16" width="26" height="32" rx="3"/><circle class="badge__cut" cy="4" r="8"/>
        </g>
        <g transform="translate(210 480)">
          <text><textPath href="#arcF" startOffset="50%" text-anchor="middle">DUST MITE &amp; BED BUG DEFENSE</textPath></text>
          <circle class="badge__disc" r="40"/><circle class="badge__ring" r="33"/>
          <ellipse class="badge__glyph" rx="8" ry="11"/><path class="badge__line" d="M-8-4h-7M8-4h7M-8 4h-7M8 4h7" stroke-width="2"/><path class="badge__line" d="M-16 16L16-16" stroke-width="3"/>
        </g>
        <g transform="translate(335 480)">
          <text><textPath href="#arcF" startOffset="50%" text-anchor="middle">ALLERGEN FREE</textPath></text>
          <circle class="badge__disc" r="40"/><circle class="badge__ring" r="33"/>
          <circle class="badge__line" r="15" stroke-width="2.5"/><circle class="badge__glyph" cx="-5" cy="-4" r="2.5"/><circle class="badge__glyph" cx="5" cy="-2" r="2"/><circle class="badge__glyph" cx="-1" cy="6" r="2.5"/>
        </g>
        <g transform="translate(460 480)">
          <text><textPath href="#arcF" startOffset="50%" text-anchor="middle">BACTERIA/MOLD/MILDEW FREE</textPath></text>
          <circle class="badge__disc" r="40"/><circle class="badge__ring" r="33"/>
          <circle class="badge__glyph" r="10"/><path class="badge__line" d="M0-17V17M-17 0H17M-12-12L12 12M-12 12L12-12" stroke-width="2.5"/>
        </g>
      </g>
    </svg>

    <p class="fits">Fits Cal King Matress</p>
  </section>

</main>
</body>
</html>
```